Sickle Cell Patient Flyer

I need this be appealing to families dealing with sickle cell disease. Both informative-introducing the idea that a stroke prevention program is not only easy for their children but necessary. Stroke is a risk to all with children with SCD.
I included a few info flyers from the Vessel Alliance and licensed to me photos I like. I am open to suggestions.
web address is brightpathwellbeing.net
Call to schedule 833-412-7086
TCD is a safe and accurate tool that makes stroke prevention possible for your SCD patients and family.
Risk is highest for SCD sufferers age 2 to 5. Protect your childs future.

Target Market(s)

Parents, families and medical professionals

Industry/Entity Type

Medical wellness

Font styles to use
Other font styles liked:
• something close to my logo font

Colors
0094D4
00A9DD
6FCCEA
C7EBF8
E9F6FB

Requirements
Nice to have
• pictures of kids (Children of color) pictures of Brains, kids happy with medical professionals
Should not have
• dark colors

```html
<!DOCTYPE html>
<html lang="en">
<head>
<meta charset="UTF-8">
<title>Stroke Prevention for Children with Sickle Cell Disease</title>
<link href="https://fonts.googleapis.com/css2?family=Poppins:wght@400;500;600;700&family=Mystery+Quest&display=swap" rel="stylesheet">
<style>
  :root {
    --navy: #0d3666;
    --mint: #6fd3ad;
    --sky: #4a9bd8;
    --ink: #232323;
    --white: #ffffff;
    --halo: rgba(13, 54, 102, 0.22);
  }
  * { margin: 0; padding: 0; box-sizing: border-box; }
  html, body { width: 931px; height: 1200px; overflow: hidden; background: var(--white); }
  body { font-family: "Poppins", sans-serif; color: var(--ink); }
  .flyer { position: relative; width: 931px; height: 1200px; overflow: hidden; }
  .backdrop { position: absolute; inset: 0; }
  .hero-image {
    position: absolute; left: 355px; top: 0; width: 576px; height: 450px;
    background: radial-gradient(ellipse at 68% 62%, #8a9099 0%, #4d5866 32%, rgba(13,54,102,0) 62%),
                linear-gradient(180deg, #1c4676 0%, var(--navy) 100%);
  }
  .brand {
    position: absolute; left: 65px; top: 82px; width: 150px;
    font-family: "Poppins", sans-serif; font-weight: 700; font-size: 24px; line-height: 1.15;
    color: var(--mint); display: flex; align-items: flex-start; gap: 8px;
  }
  .brand-mark { width: 14px; height: 14px; margin-top: 7px; background: var(--mint); flex: none; }
  .headline { position: absolute; left: 65px; top: 205px; font-size: 33px; font-weight: 700; line-height: 37px; color: var(--white); }
  .headline .soft { font-weight: 400; color: var(--mint); }
  .headline .soft-blue { font-weight: 400; color: #7db6e6; }
  .display { font-family: "Mystery Quest", cursive; color: var(--navy); }
  .band-disease {
    position: absolute; left: 65px; top: 298px; width: 450px; height: 54px;
    background: var(--mint); font-size: 42px; line-height: 54px; padding-left: 22px;
  }
  .band-possible {
    position: absolute; left: 77px; top: 357px; width: 263px; height: 58px;
    background: var(--sky); color: var(--white); font-size: 42px; line-height: 58px; padding-left: 14px;
  }
  .screening-title { position: absolute; left: 65px; top: 488px; font-size: 37px; font-weight: 700; line-height: 42px; color: var(--white); }
  .screening-title .navy { color: var(--navy); }
  .screening-title .light { font-weight: 400; }
  .divider-v { position: absolute; left: 483px; top: 505px; width: 3px; height: 95px; background: var(--sky); }
  .tcd-note { position: absolute; left: 505px; top: 493px; width: 360px; font-size: 24px; font-weight: 500; line-height: 29.5px; color: var(--ink); }
  .feature { position: absolute; top: 645px; width: 200px; text-align: center; }
  .feature-icon { position: relative; width: 132px; height: 132px; margin: 0 auto; }
  .feature-text { margin-top: 20px; font-size: 18px; font-weight: 500; line-height: 21px; color: var(--ink); }
  .feature.one { left: 89px; }
  .feature.two { left: 370px; }
  .feature.three { left: 647px; }
  .rule { position: absolute; top: 790px; width: 1px; height: 140px; background: #d8d8d8; }
  .protect { position: absolute; left: 70px; top: 968px; font-size: 52px; line-height: 56px; color: var(--mint); }
  .cta-label { position: absolute; left: 454px; top: 993px; font-size: 29px; font-weight: 600; letter-spacing: 0.5px; color: #333; }
  .phone-box {
    position: absolute; left: 454px; top: 1008px; width: 409px; height: 75px; margin-top: 33px;
    background: var(--sky); display: flex; align-items: center; gap: 14px; padding-left: 18px;
  }
  .phone-number { font-family: "Mystery Quest", cursive; font-size: 50px; color: var(--white); line-height: 1; }
  .footer { position: absolute; left: 73px; top: 1118px; width: 800px; display: flex; align-items: center; }
  .footer-note { font-size: 16px; color: var(--ink); }
  .footer-url { display: flex; align-items: center; gap: 6px; margin-left: 20px; font-size: 25px; letter-spacing: 1px; color: var(--navy); }
  .footer-url strong { font-weight: 700; }
</style>
</head>
<body>
<main class="flyer">
  <svg class="backdrop" width="931" height="1200" viewBox="0 0 931 1200" aria-hidden="true">
    <rect x="0" y="0" width="931" height="460" fill="var(--navy)"/>
    <path d="M0 442 Q470 440 931 438 L931 712 Q470 708 0 716 Z" fill="var(--mint)"/>
  </svg>

  <div class="hero-image" role="img" aria-label="Smiling young boy in a white shirt beneath a large white line drawing of a brain"></div>

  <div class="brand"><span class="brand-mark"></span><span>BrightPath Wellbeing</span></div>

  <h1 class="headline">Stroke Prevention <span class="soft">for</span><br>Children <span class="soft-blue">with</span></h1>
  <div class="band-disease display">SICKLE CELL DISEASE</div>
  <div class="band-possible display">IS POSSIBLE!</div>

  <h2 class="screening-title">Simple <span class="light">&amp;</span> painless<br>screening for<br><span class="navy">your child</span></h2>
  <div class="divider-v"></div>
  <p class="tcd-note">TCD is a safe and accurate tool that makes stroke prevention possible for your SCD patients and family.</p>

  <div class="feature one">
    <svg class="feature-icon" viewBox="0 0 132 132" aria-hidden="true">
      <circle cx="62" cy="68" r="64" fill="var(--halo)"/>
      <circle cx="66" cy="64" r="58" fill="var(--navy)"/>
      <g fill="none" stroke="#fff" stroke-width="2.5" stroke-linejoin="round">
        <rect x="42" y="40" width="48" height="36" rx="3"/>
        <rect x="49" y="47" width="34" height="22"/>
        <path d="M54 64 Q66 48 78 64"/>
        <path d="M60 76 L58 84 L74 84 L72 76"/>
        <line x1="50" y1="88" x2="90" y2="88"/>
      </g>
    </svg>
    <p class="feature-text">Our Screening<br>uses ultrasound<br>which is<br>transcranial<br>doppler.</p>
  </div>
  <div class="rule" style="left:323px"></div>
  <div class="feature two">
    <svg class="feature-icon" viewBox="0 0 132 132" aria-hidden="true">
      <circle cx="62" cy="68" r="64" fill="var(--halo)"/>
      <circle cx="66" cy="64" r="58" fill="var(--navy)"/>
      <g fill="none" stroke="#fff" stroke-width="2.5" stroke-linejoin="round">
        <rect x="42" y="38" width="36" height="50" rx="3"/>
        <rect x="53" y="34" width="14" height="8"/>
        <rect x="47" y="50" width="6" height="6"/><line x1="57" y1="53" x2="72" y2="53"/>
        <rect x="47" y="62" width="6" height="6"/><line x1="57" y1="65" x2="72" y2="65"/>
        <rect x="47" y="74" width="6" height="6"/><line x1="57" y1="77" x2="66" y2="77"/>
        <path d="M72 70 L72 82 Q72 90 80 90 Q88 90 88 82 L88 74"/>
        <circle cx="88" cy="70" r="4"/>
      </g>
    </svg>
    <p class="feature-text">Screening or early<br>signs of stroke can<br>be a tool to for early<br>diagnosis allowing<br>for treatments that<br>eliminate the risk.</p>
  </div>
  <div class="rule" style="left:616px"></div>
  <div class="feature three">
    <svg class="feature-icon" viewBox="0 0 132 132" aria-hidden="true">
      <circle cx="62" cy="68" r="64" fill="var(--halo)"/>
      <circle cx="66" cy="64" r="58" fill="var(--navy)"/>
      <g fill="none" stroke="#fff" stroke-width="2.5" stroke-linejoin="round">
        <path d="M46 66 Q38 58 46 50 Q46 40 58 40 Q66 34 74 40 Q86 38 88 50 Q96 58 88 68 Q86 78 74 76 L70 86 L64 76 Q52 80 46 66 Z"/>
        <path d="M68 46 L62 60 L70 60 L64 72"/>
      </g>
    </svg>
    <p class="feature-text">About 11% of SCD<br>patients have<br>strokes before age<br>20 with the highest<br>risk between<br>age 2 &amp;5</p>
  </div>

  <p class="protect display">PROTECT YOUR<br>CHILDS FUTURE</p>

  <p class="cta-label">CALL TO SCHEDULE</p>
  <div class="phone-box">
    <svg width="40" height="40" viewBox="0 0 24 24" aria-hidden="true">
      <path fill="var(--navy)" d="M6.6 10.8a15.1 15.1 0 0 0 6.6 6.6l2.2-2.2c.3-.3.7-.4 1-.2 1.1.4 2.3.6 3.6.6.6 0 1 .4 1 1V20c0 .6-.4 1-1 1C10.6 21 3 13.4 3 4c0-.6.4-1 1-1h3.5c.6 0 1 .4 1 1 0 1.3.2 2.5.6 3.6.1.3 0 .7-.2 1z"/>
      <path fill="none" stroke="var(--navy)" stroke-width="1.6" d="M14.5 3.5a6 6 0 0 1 6 6M14.5 7a2.6 2.6 0 0 1 2.6 2.6"/>
    </svg>
    <span class="phone-number">833-412-7086</span>
  </div>

  <div class="footer">
    <span class="footer-note">Visit our website for more information</span>
    <span class="footer-url">
      <svg width="18" height="18" viewBox="0 0 20 20" aria-hidden="true">
        <g fill="none" stroke="var(--mint)" stroke-width="1.6"><circle cx="10" cy="10" r="8"/><ellipse cx="10" cy="10" rx="3.5" ry="8"/><line x1="2" y1="10" x2="18" y2="10"/></g>
      </svg>
      <span>www.<strong>brightpathwellbeing</strong>.net</span>
    </span>
  </div>
</main>
</body>
</html>
```